Business Card Design

New business card design

Target Market(s)

Residential & Commercial Property Managers

Industry/Entity Type

Plumbing Services

Contact Information for Business Card

Name - Rowan Keddle, title - Director, Phone Number - 0431 286 517, email - rowan@tbk-plumbing.com.au, Company ABN - 73 215 904 386,

Font styles to use
Sans Serif

Colors
0054AA
0677BA
7BADD7
CADEEF
E8F1F8

```html
<!DOCTYPE html>
<html lang="en">
<head>
<meta charset="utf-8">
<title>TBK Plumbing Services – Business Cards</title>
<link href="https://fonts.googleapis.com/css2?family=Poppins:wght@300;400;500&display=swap" rel="stylesheet">
<style>
  :root {
    --stage: #222222;
    --card-white: #ffffff;
    --brand-blue: #27a8e1;
    --brand-blue-deep: #1d8cc0;
    --ink: #1c2630;
    --taupe: #7a7068;
  }
  * { margin: 0; padding: 0; box-sizing: border-box; }
  html, body {
    width: 1200px; height: 780px; overflow: hidden;
    background: var(--stage);
    font-family: "Poppins", Arial, sans-serif;
  }
  .stage { position: relative; width: 1200px; height: 780px; }
  .card {
    position: absolute; top: 240px;
    width: 520px; height: 300px;
    overflow: hidden;
    box-shadow: 0 14px 30px rgba(0,0,0,.45);
  }
  .card--front { left: 50px; background: var(--card-white); }
  .card--back  { left: 630px; background: var(--brand-blue); }

  .card__wave { position: absolute; inset: 0; width: 100%; height: 100%; }

  .company-name {
    position: absolute;
    font-size: 22px; font-weight: 400; line-height: 1.2;
    white-space: nowrap; text-align: center;
  }
  .card--front .company-name { left: 210px; top: 56px; width: 290px; color: var(--ink); }
  .card--back .company-name {
    left: 0; top: 132px; width: 520px;
    font-size: 30px; color: var(--brand-blue-deep);
  }

  .person { position: absolute; left: 58px; top: 118px; text-align: right; }
  .person__name { font-size: 24px; font-weight: 300; color: var(--taupe); line-height: 1.15; white-space: nowrap; }
  .person__first { color: var(--brand-blue); font-weight: 500; }
  .person__title { font-size: 12px; font-weight: 400; color: var(--ink); margin-top: 2px; }

  .divider {
    position: absolute; left: 252px; top: 150px;
    width: 1px; height: 66px; background: var(--brand-blue);
  }

  .contact { position: absolute; left: 268px; top: 152px; list-style: none; }
  .contact__item {
    display: flex; align-items: center; gap: 7px;
    font-size: 12.5px; color: var(--ink); line-height: 21px; white-space: nowrap;
  }
  .contact__icon { width: 11px; height: 11px; flex: none; }

  .abn {
    position: absolute; left: 22px; top: 272px;
    font-size: 12px; font-weight: 300; color: var(--card-white); letter-spacing: .3px;
  }
</style>
</head>
<body>
<main class="stage">
  <section class="card card--front" aria-label="Business card front">
    <svg class="card__wave" viewBox="0 0 520 300" aria-hidden="true">
      <path d="M0 120 C40 200 180 290 400 300 L0 300 Z" fill="var(--brand-blue)"/>
      <path d="M0 120 C40 200 180 290 400 300" fill="none" stroke="var(--card-white)" stroke-width="6"/>
      <path d="M12 116 C55 200 190 282 398 294" fill="none" stroke="var(--taupe)" stroke-width="2.2"/>
    </svg>

    <div class="company-name">TBK Plumbing Services</div>

    <div class="person">
      <div class="person__name"><span class="person__first">Rowan</span> Keddle</div>
      <div class="person__title">Director</div>
    </div>

    <div class="divider"></div>

    <ul class="contact">
      <li class="contact__item">
        <svg class="contact__icon" viewBox="0 0 12 12" aria-hidden="true"><path d="M2.5 1 L4.5 1 L5.2 3.6 L3.9 4.6 C4.6 6 6 7.4 7.4 8.1 L8.4 6.8 L11 7.5 L11 9.5 C11 10.3 10.3 11 9.5 11 C4.8 11 1 7.2 1 2.5 C1 1.7 1.7 1 2.5 1Z" fill="var(--brand-blue)"/></svg>
        0431 286 517
      </li>
      <li class="contact__item">
        <svg class="contact__icon" viewBox="0 0 12 12" aria-hidden="true"><circle cx="6" cy="6" r="5" fill="none" stroke="var(--brand-blue)" stroke-width="1.3"/><path d="M1 6 H11 M6 1 C3.5 4 3.5 8 6 11 M6 1 C8.5 4 8.5 8 6 11" fill="none" stroke="var(--brand-blue)" stroke-width="1"/></svg>
        www.tbk-plumbing.com.au
      </li>
      <li class="contact__item">
        <svg class="contact__icon" viewBox="0 0 12 12" aria-hidden="true"><rect x="1" y="2.5" width="10" height="7" rx="1" fill="var(--brand-blue)"/><path d="M1.5 3 L6 6.5 L10.5 3" fill="none" stroke="var(--card-white)" stroke-width="1"/></svg>
        rowan@tbk-plumbing.com.au
      </li>
    </ul>

    <div class="abn">ABN - 73 215 904 386</div>
  </section>

  <section class="card card--back" aria-label="Business card back">
    <div class="company-name">TBK Plumbing Services</div>
  </section>
</main>
</body>
</html>
```